Diabetes control iOS/Android app design

I need a modern app design with light colors that are easy on the eyes, This app is for diabetes control. Focusing on Sweet/carb control and its daily intake .. I have uploaded some wireframe pages to design . Light colors are preferred for design. I donot need too much Hussle and data on main page.
Name/title: Glimwell- Diabetes reversal

Target Market(s)

Diabetes patients

Industry/Entity Type

health

Colors
0094D4
00A9DD
6FCCEA
C7EBF8
E9F6FB
00AB8E
00BBA5
67D7C9
C6EFE9
E9F9F6
59FF00
82FF00
B8FF75
E3FFCB
F4FFEA
FFC000
F8CF3A
FAE287
FDF2CF
FEFAEE

Requirements
Should not have
• complicated design. It should be simple , modern and easy o eye.

```html
<!DOCTYPE html>
<html lang="en">
<head>
<meta charset="utf-8">
<title>Glimwell - Diabetes reversal app screens</title>
<link href="https://fonts.googleapis.com/css2?family=Outfit:wght@400;500;600;700&display=swap" rel="stylesheet">
<style>
:root{
  --canvas:#e4fdf7;
  --white:#ffffff;
  --ink:#111a17;
  --muted:#5b6663;
  --teal:#00ab8e;
  --teal-deep:#0e8a66;
  --green:#59ff00;
  --green-soft:#6ef047;
  --green-pale:#d8fbc6;
  --mint:#e9f9f6;
  --mint-ring:#e4fbf6;
  --amber:#f8c035;
  --head-a:#55de3c;
  --head-b:#17a05c;
  --head-c:#0f8e68;
}
*{box-sizing:border-box;margin:0;padding:0}
html,body{width:1200px;height:747px;overflow:hidden;background:var(--canvas);font-family:"Outfit",sans-serif;color:var(--ink)}
.screen{position:absolute;top:75px;width:309px;height:597px;background:var(--white);border-radius:30px;overflow:hidden;box-shadow:0 10px 30px rgba(20,120,90,.12)}
.screen--sugar{left:80px}
.screen--monitor{left:453px}
.screen--plan{left:825px}
.app-header{position:absolute;left:0;top:0;width:100%;height:117px;border-radius:30px 30px 40px 40px;background:linear-gradient(160deg,var(--head-a) 0%,var(--head-b) 55%,var(--head-c) 100%);color:var(--white)}
.screen--sugar .app-header{height:126px}
.status-time{position:absolute;left:15px;top:20px;font-size:9px;font-weight:600}
.status-icons{position:absolute;right:14px;top:20px}
.app-title{position:absolute;left:15px;top:55px;font-size:17px;line-height:23px;font-weight:400}
.app-title b{font-weight:700}
.menu-icon{position:absolute;right:15px;top:71px}
.section-title{position:absolute;left:0;width:100%;text-align:center;font-size:18px;font-weight:600;letter-spacing:.2px}
.section-title span{color:var(--teal)}
.abs{position:absolute}
.count-label{position:absolute;left:0;width:100%;text-align:center;top:263px;font-size:12px;line-height:16px;color:var(--teal);font-weight:500}
.gauge-label{position:absolute;font-size:12px;color:var(--ink)}
.chart-sub{position:absolute;top:159px;width:100%;text-align:center;font-size:10.5px;color:#333}
.legend{position:absolute;top:510px;font-size:10.5px;font-weight:500;display:flex;align-items:center;gap:5px}
.legend i{width:8px;height:8px;border:1.5px solid var(--teal);border-radius:50%}
.rehab-btn{position:absolute;left:96px;top:268px;width:117px;height:34px;border-radius:17px;background:var(--amber);font-size:13.5px;font-weight:500;display:flex;align-items:center;justify-content:center;box-shadow:0 4px 8px rgba(200,150,0,.25)}
.plan-card{position:absolute;left:7px;top:334px;width:296px;height:263px;border-radius:28px 28px 0 0;background:linear-gradient(180deg,#e3f8f3 0%,#f7fdfb 55%,#ffffff 100%);text-align:center}
.plan-card h3{margin-top:20px;font-size:13.5px;line-height:23px;font-weight:500}
.plan-card h3 span{color:var(--teal)}
.plan-card p{margin-top:8px;font-size:10px;color:#333}
.plan-steps{list-style:none;margin-top:12px;font-size:12.5px;line-height:30px}
.plan-steps li::before{content:"\2714";color:var(--teal);margin-right:4px;font-size:11px}
.tab-bar{position:absolute;left:0;bottom:0;width:100%;height:41px;border-radius:0 0 30px 30px;background:linear-gradient(180deg,var(--head-c) 0%,var(--head-b) 50%,var(--head-a) 100%)}
.tab-rr{position:absolute;left:44px;top:14px;font-size:11px;font-weight:600;color:var(--white)}
.tab-add{position:absolute;left:135px;top:-22px;width:38px;height:38px;border-radius:50%;background:var(--teal-deep);border:3px solid var(--white);display:flex;align-items:center;justify-content:center}
</style>
</head>
<body>

<!-- Screen 1: sugar count -->
<section class="screen screen--sugar">
  <header class="app-header">
    <div class="status-time">10.00 AM</div>
    <svg class="status-icons" width="48" height="9" viewBox="0 0 48 9" fill="#fff"><rect x="0" y="6" width="2" height="3"/><rect x="3" y="4" width="2" height="5"/><rect x="6" y="2" width="2" height="7"/><path d="M18 8l-2-2a3 3 0 0 1 4 0zM14 4.5a6 6 0 0 1 8 0l-1 1a4.6 4.6 0 0 0-6 0zM12.5 3a8 8 0 0 1 11 0l-1 1a6.6 6.6 0 0 0-9 0z"/><rect x="34" y="2" width="11" height="6" rx="1.5"/><rect x="45.5" y="4" width="1.5" height="2"/></svg>
    <h1 class="app-title"><b>GLIMWELL-</b> Diabetes<br>reversal</h1>
    <svg class="menu-icon" width="18" height="14" viewBox="0 0 18 14" stroke="#fff" stroke-width="1.8" stroke-linecap="round"><line x1="1" y1="2" x2="17" y2="2"/><line x1="6" y1="7" x2="17" y2="7"/><line x1="1" y1="12" x2="17" y2="12"/></svg>
  </header>

  <h2 class="section-title" style="top:160px">SUGAR <span>COUNT</span></h2>
  <svg class="abs" style="left:0;top:0" width="309" height="597" viewBox="0 0 309 597">
    <circle cx="154" cy="260" r="55" fill="none" stroke="var(--mint-ring)" stroke-width="10"/>
    <path d="M99 266 A55 55 0 1 1 209 266" fill="none" stroke="var(--green-soft)" stroke-width="10" stroke-linecap="round"/>
    <rect x="132" y="222" width="45" height="36" rx="8" fill="#e9eeee" role="img" aria-label="Photo of white sugar cubes"/>
    <!-- consumption gauge -->
    <path d="M94 489 A60 60 0 0 1 214 489" fill="none" stroke="var(--green-soft)" stroke-width="14"/>
    <g stroke="#fff" stroke-width="2">
      <line x1="101" y1="455" x2="113" y2="462"/>
      <line x1="154" y1="425" x2="154" y2="440"/>
      <line x1="207" y1="455" x2="195" y2="462"/>
    </g>
    <g font-family="Outfit, sans-serif" font-size="10" fill="#9aa3a0" text-anchor="middle">
      <text x="113" y="490">1</text><text x="124" y="463">2</text><text x="153" y="453">3</text><text x="181" y="463">4</text><text x="197" y="490">5</text>
    </g>
    <g stroke="var(--green-soft)" stroke-width="2" fill="none" stroke-linecap="round"><line x1="154" y1="414" x2="154" y2="440"/><polyline points="148,420 154,414 160,420"/></g>
  </svg>
  <div class="count-label">1 Sugar today<br>bites</div>

  <h2 class="section-title" style="top:357px">CONSUMPTION <span>TODAY</span></h2>
  <div class="gauge-label" style="left:140px;top:396px">Fatal</div>
  <div class="gauge-label" style="left:64px;top:493px">Danger</div>
  <div class="gauge-label" style="left:201px;top:493px">Catastrophe</div>

  <nav class="tab-bar">
    <span class="tab-rr">RR</span>
    <svg class="abs" style="left:93px;top:13px" width="12" height="15" viewBox="0 0 12 15" fill="#fff"><path d="M0 1a1 1 0 0 1 1-1h6l5 5v9a1 1 0 0 1-1 1H1a1 1 0 0 1-1-1z"/><g stroke="var(--head-b)" stroke-width="1"><line x1="2.5" y1="7" x2="9.5" y2="7"/><line x1="2.5" y1="9.5" x2="9.5" y2="9.5"/><line x1="2.5" y1="12" x2="9.5" y2="12"/></g></svg>
    <div class="tab-add"><svg width="18" height="18" viewBox="0 0 18 18" stroke="#fff" stroke-width="2.4" stroke-linecap="round"><line x1="9" y1="2" x2="9" y2="16"/><line x1="2" y1="9" x2="16" y2="9"/></svg></div>
    <svg class="abs" style="left:202px;top:13px" width="13" height="15" viewBox="0 0 13 15" fill="#fff"><rect x="3" y="0" width="10" height="12" rx="1"/><rect x="0" y="3" width="10" height="12" rx="1" stroke="var(--head-b)"/><g stroke="var(--head-b)" stroke-width="1"><line x1="2" y1="7" x2="8" y2="7"/><line x1="2" y1="9.5" x2="8" y2="9.5"/><line x1="2" y1="12" x2="8" y2="12"/></g></svg>
    <svg class="abs" style="left:246px;top:10px" width="18" height="20" viewBox="0 0 18 20" fill="none" stroke="#fff" stroke-width="2" stroke-linecap="round"><circle cx="7" cy="2.5" r="2" fill="#fff" stroke="none"/><path d="M7 6l-1 6 3 4v3M6 12l-3 7M7 7l4 3M12 10l4 9"/></svg>
  </nav>
</section>

<!-- Screen 2: rehab monitor -->
<section class="screen screen--monitor">
  <header class="app-header">
    <div class="status-time">10.00 AM</div>
    <svg class="status-icons" width="48" height="9" viewBox="0 0 48 9" fill="#fff"><rect x="0" y="6" width="2" height="3"/><rect x="3" y="4" width="2" height="5"/><rect x="6" y="2" width="2" height="7"/><path d="M18 8l-2-2a3 3 0 0 1 4 0zM14 4.5a6 6 0 0 1 8 0l-1 1a4.6 4.6 0 0 0-6 0zM12.5 3a8 8 0 0 1 11 0l-1 1a6.6 6.6 0 0 0-9 0z"/><rect x="34" y="2" width="11" height="6" rx="1.5"/><rect x="45.5" y="4" width="1.5" height="2"/></svg>
    <h1 class="app-title"><b>GLIMWELL-</b> Diabetes<br>reversal</h1>
    <svg class="menu-icon" width="18" height="14" viewBox="0 0 18 14" stroke="#fff" stroke-width="1.8" stroke-linecap="round"><line x1="1" y1="2" x2="17" y2="2"/><line x1="6" y1="7" x2="17" y2="7"/><line x1="1" y1="12" x2="17" y2="12"/></svg>
  </header>

  <h2 class="section-title" style="top:129px;font-size:17px">REHAB <span>MONITOR</span></h2>
  <div class="chart-sub">Daily Sugar Graph (Fasting + Random)</div>

  <svg class="abs" style="left:0;top:0" width="309" height="597" viewBox="0 0 309 597" font-family="Outfit, sans-serif">
    <!-- sugar line chart -->
    <g font-size="6.5" fill="#222" text-anchor="middle">
      <text x="19" y="191">60</text><text x="19" y="209">50</text><text x="19" y="225">40</text><text x="19" y="244">30</text><text x="19" y="261">20</text><text x="19" y="278">10</text><text x="19" y="295">0</text>
    </g>
    <g stroke="#eef2f1" stroke-width="1">
      <line x1="56" y1="185" x2="56" y2="294"/><line x1="98" y1="185" x2="98" y2="294"/><line x1="141" y1="185" x2="141" y2="294"/><line x1="183" y1="185" x2="183" y2="294"/><line x1="224" y1="185" x2="224" y2="294"/><line x1="266" y1="185" x2="266" y2="294"/>
    </g>
    <path d="M29 218 L52 221 L66 223 L98 247 L132 232 L153 242 L170 232 L178 218 L208 221 L221 214 L246 229 L266 217 L293 226 L293 294 L29 294Z" fill="#f0fde6"/>
    <path d="M29 253 L66 276 L98 268 L132 279 L153 268 L178 261 L197 268 L221 257 L246 272 L266 261 L293 265 L293 294 L29 294Z" fill="var(--green-pale)" opacity=".9"/>
    <polyline points="29,218 52,221 66,223 98,247 132,232 153,242 170,232 178,218 208,221 221,214 246,229 266,217 293,226" fill="none" stroke="var(--teal-deep)" stroke-width="1.3"/>
    <g fill="var(--teal-deep)"><circle cx="52" cy="221" r="2"/><circle cx="98" cy="247" r="2"/><circle cx="153" cy="242" r="2"/><circle cx="178" cy="218" r="2"/><circle cx="221" cy="214" r="2"/><circle cx="266" cy="217" r="2"/></g>
    <g fill="#8fe0cf"><circle cx="66" cy="223" r="2"/><circle cx="132" cy="232" r="2"/><circle cx="170" cy="232" r="2"/><circle cx="208" cy="221" r="2"/><circle cx="246" cy="229" r="2"/></g>
    <rect x="75" y="198" width="59" height="27" rx="5" fill="#fff" stroke="#eef1f0"/>
    <path d="M96 225 L100 230 L104 225Z" fill="#fff"/>
    <g font-size="4.5" text-anchor="middle"><text x="104" y="206" font-weight="600">January 02,2025</text><text x="104" y="213">200 kg</text><text x="104" y="220" fill="var(--teal)">View All</text></g>
    <g font-size="7" fill="#222" text-anchor="middle">
      <text x="56" y="309">Mon</text><text x="98" y="309">Tue</text><text x="141" y="309">Wed</text><text x="183" y="309">Thrus</text><text x="224" y="309">Fri</text><text x="266" y="309">Sat</text>
    </g>

    <!-- walk bar chart -->
    <g font-size="6.5" fill="#666" text-anchor="middle">
      <text x="19" y="365">40</text><text x="19" y="396">30</text><text x="19" y="421">20</text><text x="19" y="449">10</text><text x="19" y="477">0</text>
    </g>
    <g stroke="#eef2f1" stroke-width="1">
      <rect x="29" y="362" width="252" height="113" fill="none"/>
      <line x1="29" y1="390" x2="281" y2="390"/><line x1="29" y1="418" x2="281" y2="418"/><line x1="29" y1="446" x2="281" y2="446"/>
      <line x1="66" y1="362" x2="66" y2="475"/><line x1="100" y1="362" x2="100" y2="475"/><line x1="135" y1="362" x2="135" y2="475"/><line x1="172" y1="362" x2="172" y2="475"/><line x1="207" y1="362" x2="207" y2="475"/><line x1="242" y1="362" x2="242" y2="475"/>
    </g>
    <g fill="#c7f3e9">
      <rect x="44" y="436" width="6" height="26"/><rect x="81" y="436" width="6" height="26"/><rect x="113" y="414" width="6" height="24"/><rect x="150" y="436" width="6" height="26"/><rect x="187" y="427" width="6" height="26"/><rect x="222" y="441" width="6" height="26"/><rect x="256" y="427" width="6" height="26"/>
    </g>
    <g fill="var(--green-soft)">
      <rect x="44" y="410" width="6" height="26" rx="1"/><rect x="81" y="395" width="6" height="41" rx="1"/><rect x="113" y="386" width="6" height="28" rx="1"/><rect x="150" y="410" width="6" height="26" rx="1"/><rect x="187" y="399" width="6" height="28" rx="1"/><rect x="222" y="414" width="6" height="27" rx="1"/><rect x="256" y="378" width="6" height="49" rx="1"/>
    </g>
    <g font-size="7" fill="#222" text-anchor="middle">
      <text x="48" y="489">Mon</text><text x="84" y="489">Tue</text><text x="116" y="489">Wed</text><text x="153" y="489">Thrus</text><text x="190" y="489">Fri</text><text x="225" y="489">Sat</text><text x="260" y="489">Sun</text>
    </g>
  </svg>

  <h2 class="section-title" style="top:327px;font-size:17px">DAILY WALK/<span>EXERCISE</span></h2>
  <div class="legend" style="left:34px"><i></i>Sugar Bite Sent Weekly</div>
  <div class="legend" style="left:203px"><i></i>Weekly Avg.</div>

  <nav class="tab-bar">
    <span class="tab-rr">RR</span>
    <svg class="abs" style="left:93px;top:13px" width="12" height="15" viewBox="0 0 12 15" fill="#fff"><path d="M0 1a1 1 0 0 1 1-1h6l5 5v9a1 1 0 0 1-1 1H1a1 1 0 0 1-1-1z"/><g stroke="var(--head-b)" stroke-width="1"><line x1="2.5" y1="7" x2="9.5" y2="7"/><line x1="2.5" y1="9.5" x2="9.5" y2="9.5"/><line x1="2.5" y1="12" x2="9.5" y2="12"/></g></svg>
    <div class="tab-add"><svg width="18" height="18" viewBox="0 0 18 18" stroke="#fff" stroke-width="2.4" stroke-linecap="round"><line x1="9" y1="2" x2="9" y2="16"/><line x1="2" y1="9" x2="16" y2="9"/></svg></div>
    <svg class="abs" style="left:202px;top:13px" width="13" height="15" viewBox="0 0 13 15" fill="#fff"><rect x="3" y="0" width="10" height="12" rx="1"/><rect x="0" y="3" width="10" height="12" rx="1" stroke="var(--head-b)"/><g stroke="var(--head-b)" stroke-width="1"><line x1="2" y1="7" x2="8" y2="7"/><line x1="2" y1="9.5" x2="8" y2="9.5"/><line x1="2" y1="12" x2="8" y2="12"/></g></svg>
    <svg class="abs" style="left:246px;top:10px" width="18" height="20" viewBox="0 0 18 20" fill="none" stroke="#fff" stroke-width="2" stroke-linecap="round"><circle cx="7" cy="2.5" r="2" fill="#fff" stroke="none"/><path d="M7 6l-1 6 3 4v3M6 12l-3 7M7 7l4 3M12 10l4 9"/></svg>
  </nav>
</section>

<!-- Screen 3: rehab plan -->
<section class="screen screen--plan">
  <header class="app-header">
    <div class="status-time">10.00 AM</div>
    <svg class="status-icons" width="48" height="9" viewBox="0 0 48 9" fill="#fff"><rect x="0" y="6" width="2" height="3"/><rect x="3" y="4" width="2" height="5"/><rect x="6" y="2" width="2" height="7"/><path d="M18 8l-2-2a3 3 0 0 1 4 0zM14 4.5a6 6 0 0 1 8 0l-1 1a4.6 4.6 0 0 0-6 0zM12.5 3a8 8 0 0 1 11 0l-1 1a6.6 6.6 0 0 0-9 0z"/><rect x="34" y="2" width="11" height="6" rx="1.5"/><rect x="45.5" y="4" width="1.5" height="2"/></svg>
    <h1 class="app-title"><b>GLIMWELL-</b> Diabetes<br>reversal</h1>
    <svg class="menu-icon" width="18" height="14" viewBox="0 0 18 14" stroke="#fff" stroke-width="1.8" stroke-linecap="round"><line x1="1" y1="2" x2="17" y2="2"/><line x1="6" y1="7" x2="17" y2="7"/><line x1="1" y1="12" x2="17" y2="12"/></svg>
  </header>

  <h2 class="section-title" style="top:143px">REHAB <span>PLAN</span></h2>
  <svg class="abs" style="left:125px;top:187px" width="60" height="60" viewBox="0 0 60 60" font-family="Outfit, sans-serif">
    <circle cx="30" cy="30" r="27" fill="none" stroke="var(--mint-ring)" stroke-width="4"/>
    <path d="M3 34 A27 27 0 1 1 57 34" fill="none" stroke="var(--green-soft)" stroke-width="4" stroke-linecap="round"/>
    <text x="30" y="37" text-anchor="middle" font-size="20" font-weight="600" fill="var(--teal)">R</text>
  </svg>
  <div class="rehab-btn">Rehab Plan</div>

  <div class="plan-card">
    <h3>See your plan to <span>achieve no medicine<br>diabetes control</span></h3>
    <p>See your plan to achieve no medicine diabetes control</p>
    <ul class="plan-steps">
      <li>Choose desired date</li>
      <li>Follow suggested diet</li>
      <li>Enter your readings (Sugar, Frequency, Diet)</li>
    </ul>
  </div>

  <nav class="tab-bar">
    <span class="tab-rr">RR</span>
    <svg class="abs" style="left:93px;top:13px" width="12" height="15" viewBox="0 0 12 15" fill="#fff"><path d="M0 1a1 1 0 0 1 1-1h6l5 5v9a1 1 0 0 1-1 1H1a1 1 0 0 1-1-1z"/><g stroke="var(--head-b)" stroke-width="1"><line x1="2.5" y1="7" x2="9.5" y2="7"/><line x1="2.5" y1="9.5" x2="9.5" y2="9.5"/><line x1="2.5" y1="12" x2="9.5" y2="12"/></g></svg>
    <div class="tab-add"><svg width="18" height="18" viewBox="0 0 18 18" stroke="#fff" stroke-width="2.4" stroke-linecap="round"><line x1="9" y1="2" x2="9" y2="16"/><line x1="2" y1="9" x2="16" y2="9"/></svg></div>
    <svg class="abs" style="left:202px;top:13px" width="13" height="15" viewBox="0 0 13 15" fill="#fff"><rect x="3" y="0" width="10" height="12" rx="1"/><rect x="0" y="3" width="10" height="12" rx="1" stroke="var(--head-b)"/><g stroke="var(--head-b)" stroke-width="1"><line x1="2" y1="7" x2="8" y2="7"/><line x1="2" y1="9.5" x2="8" y2="9.5"/><line x1="2" y1="12" x2="8" y2="12"/></g></svg>
    <svg class="abs" style="left:246px;top:10px" width="18" height="20" viewBox="0 0 18 20" fill="none" stroke="#fff" stroke-width="2" stroke-linecap="round"><circle cx="7" cy="2.5" r="2" fill="#fff" stroke="none"/><path d="M7 6l-1 6 3 4v3M6 12l-3 7M7 7l4 3M12 10l4 9"/></svg>
  </nav>
</section>

</body>
</html>
```